dobbo's business card for earthmoving and tipper hire business.

I have a small earthmoving and tipper truck company. I am aiming for the smaller jobs that the big guys don't want. I am also Doing grass slashing and fire hazard reduction work. I would like to see some earthy colors, greens browns etc. I have a tractor with a front end loader attachment, and a 22 ton tipper. I would like to maybe have a silhouette of a tipper and tractor/slasher/loader setup in centre with my business name over the top and details to one side or something like that

Industry/Entity Type

Business

Contact Information for Business Card

Dobbo's small earthworks and tipper hireToowoombaABN: 47781050480PH 0479126773Email dobbo.3@farrowpost.com

Font styles to use
Sans Serif

Colors
fbee3d
abd036
85cae6
f78f20

Requirements
Nice to have
• Earthy colors . business name in blue

```html
<!DOCTYPE html>
<html lang="en">
<head>
<meta charset="utf-8">
<title>Dobbo's Earthworks and Tipper Hire – Business Card</title>
<link rel="stylesheet" href="https://fonts.googleapis.com/css2?family=Nunito:wght@800&family=Tenor+Sans&family=Questrial&family=Open+Sans:ital,wght@1,700;1,800&display=swap">
<style>
  :root {
    --rust: #8f3222;
    --rust-deep: #7e2e1f;
    --green: #2b9a45;
    --green-soft: #5e8f4a;
    --sky: #b8dcec;
    --ink: #1d3321;
    --panel-top: #8b7b72;
    --panel-bottom: #8ea2a6;
    --panel-grey: rgba(150, 148, 142, 0.9);
    --strip: #4b4541;
    --white: #f4f1ec;
  }
  * { margin: 0; padding: 0; box-sizing: border-box; }
  html, body { width: 1200px; height: 741px; overflow: hidden; background: var(--rust); }
  .card { position: relative; width: 1200px; height: 741px; overflow: hidden; background: var(--rust); }
  .backdrop { position: absolute; inset: 0; }
  .art { position: absolute; }
  .art-cab { left: 25px; top: 55px; width: 235px; height: 170px; border-radius: 14px;
    background: linear-gradient(160deg, rgba(70,110,60,.55), rgba(60,95,55,.25)); }
  .art-tractor { left: 302px; top: 185px; width: 445px; height: 190px; border-radius: 40px 40px 20px 20px;
    background: radial-gradient(ellipse at 45% 55%, rgba(150,180,120,.9), rgba(110,150,95,.55) 60%, rgba(90,140,80,0) 100%); }
  .art-truck { left: 778px; top: 175px; width: 300px; height: 210px; border-radius: 18px;
    background: linear-gradient(170deg, rgba(190,200,180,.85), rgba(150,165,140,.6)); }

  .brand { position: absolute; left: 500px; top: 36px; width: 430px; text-align: center; }
  .brand-name { font-family: 'Nunito', sans-serif; font-weight: 800; font-size: 68px; line-height: 1; color: var(--sky); letter-spacing: 1px; }
  .brand-tag { font-family: 'Tenor Sans', sans-serif; font-variant: small-caps; font-size: 30px; color: var(--white);
    letter-spacing: 2px; transform: rotate(3deg); margin-top: 4px; margin-left: -10px; white-space: nowrap; }

  .panel { position: absolute; top: 422px; width: 513px; height: 275px; border-radius: 38px; overflow: hidden;
    box-shadow: 0 4px 10px rgba(0,0,0,.25); }
  .contact { left: 41px; background: var(--panel-bottom); }
  .contact-head { height: 116px; background: var(--panel-top); text-align: center; padding-top: 6px; }
  .contact-name { font-family: 'Questrial', sans-serif; font-size: 33px; font-weight: 700; color: var(--sky); letter-spacing: 6px; }
  .contact-tag { font-family: 'Open Sans', sans-serif; font-style: italic; font-weight: 700; font-size: 15px; color: var(--ink); letter-spacing: 2px; }
  .contact-town, .contact-abn { font-family: 'Questrial', sans-serif; font-size: 17px; font-weight: 700; color: var(--ink); letter-spacing: 3px; line-height: 1.2; }
  .contact-body { text-align: center; padding-top: 30px; color: var(--ink); font-family: 'Questrial', sans-serif; font-weight: 700; }
  .contact-phone { font-size: 34px; letter-spacing: 1px; }
  .contact-phone .digits { letter-spacing: 5px; }
  .contact-email { font-size: 27px; margin-top: 22px; }

  .services { left: 641px; background: var(--panel-grey); list-style: none; padding: 14px 0 0 70px; }
  .service { display: flex; align-items: center; height: 64px; font-family: 'Open Sans', sans-serif; font-style: italic; font-weight: 800; font-size: 25px; color: var(--ink); }
  .service svg { width: 56px; height: 42px; margin-right: 14px; flex: none; }
  .service:nth-child(2), .service:nth-child(3) { padding-left: 6px; }
  .service:nth-child(4) { margin-left: -22px; }

  .base-strip { position: absolute; left: 0; bottom: 0; width: 100%; height: 8px; background: var(--strip); }
</style>
</head>
<body>
<main class="card">
  <svg class="backdrop" width="1200" height="741" viewBox="0 0 1200 741" aria-hidden="true">
    <rect width="1200" height="741" fill="var(--rust)"/>
    <path d="M0 0 H140 C 330 150, 620 185, 1200 38 V 478 C 800 380, 350 360, 0 280 Z" fill="var(--green)"/>
    <path d="M0 280 C 350 360, 800 380, 1200 478 V 741 H 0 Z" fill="var(--rust-deep)" opacity=".6"/>
  </svg>

  <div class="art art-cab" role="img" aria-label="Faint outline of a tipper truck cab"></div>
  <div class="art art-tractor" role="img" aria-label="Tractor with front end loader attachment"></div>
  <div class="art art-truck" role="img" aria-label="Tipper truck"></div>

  <header class="brand">
    <h1 class="brand-name">Dobbo's</h1>
    <p class="brand-tag">Earthworks and tipper hire</p>
  </header>

  <section class="panel contact">
    <div class="contact-head">
      <p class="contact-name">Dobbo's</p>
      <p class="contact-tag">small earthworks and tipper hire</p>
      <p class="contact-town">RIDGEVALE</p>
      <p class="contact-abn">ABN:51603928174</p>
    </div>
    <div class="contact-body">
      <p class="contact-phone">Phone: <span class="digits">0412583906</span></p>
      <p class="contact-email">Email: dobbo.3@farrowpost.com</p>
    </div>
  </section>

  <ul class="panel services">
    <li class="service">
      <svg viewBox="0 0 56 42" fill="none" stroke="var(--ink)" stroke-width="3"><path d="M4 30 V14 H14 L20 22 V30"/><path d="M20 22 L24 8 L50 12 V30 H4"/><circle cx="14" cy="32" r="4" fill="var(--ink)"/><circle cx="40" cy="32" r="4" fill="var(--ink)"/></svg>
      Tipper hire
    </li>
    <li class="service">
      <svg viewBox="0 0 56 42" fill="none" stroke="var(--ink)" stroke-width="3"><path d="M14 22 V6 H32 V20"/><path d="M8 22 H44 V30"/><circle cx="16" cy="30" r="8"/><circle cx="42" cy="33" r="5"/></svg>
      Earthmoving
    </li>
    <li class="service">
      <svg viewBox="0 0 56 42" fill="var(--ink)"><path d="M10 40 C10 26 6 14 2 8 C10 14 16 26 16 40Z"/><path d="M20 40 C20 24 22 10 26 2 C26 14 26 28 26 40Z"/><path d="M30 40 C32 26 38 14 46 8 C40 18 36 30 36 40Z"/><path d="M40 40 C42 32 48 24 54 22 C50 28 46 34 46 40Z"/></svg>
      Grass slashing
    </li>
    <li class="service">
      <svg viewBox="0 0 56 42" fill="none" stroke="var(--ink)" stroke-width="3"><circle cx="28" cy="21" r="13"/><path d="M6 10 A24 24 0 0 0 6 32"/><path d="M50 10 A24 24 0 0 1 50 32"/><path d="M28 13 C24 18 22 22 24 26 C26 29 30 29 32 26 C34 22 30 20 28 13Z" fill="var(--ink)"/></svg>
      Fire hazard reduction
    </li>
  </ul>

  <div class="base-strip"></div>
</main>
</body>
</html>
```